KTWG application splash screen

We need a 1024x768 image for use as an application splash screen.
The image will be displayed full screen on an 10 inch industrial PC 1024x768 screen while our application is launching. The image should convey that the application is "Waiting for connection to Wi-Fi access point..." and include a graphic of the industrial PC connected to the access point via an Ethernet cable. A list of troubleshooting steps should be included at the bottom of the image. The troubleshooting steps should not be the main focus of the image and should be shown in a smaller font (but still readable at 1024x768 displayed on a 10 inch screen).
I will include a mock up of the general idea of what we are looking for as well as image files for the industrial PC, a screenshot of our application to show on the PC's screen and the AP.
For general look and feel and a sense of corporate branding please review our website https://marrowgatesoilworks.example/. The splash screen should reflect corporate branding.
Target Market(s)
Users of our application
Industry/Entity Type
Agriculture
Look and feel

```html
<!DOCTYPE html>
<html lang="en">
<head>
<meta charset="utf-8">
<title>KTWG splash screen</title>
<link href="https://fonts.googleapis.com/css2?family=Poppins:wght@400;500;600;700&display=swap" rel="stylesheet">
<style>
:root{
  --brand-green:#0f8a12;
  --bright-green:#1cff1c;
  --deep-green:#0a5a14;
  --white:#ffffff;
  --ink:#111111;
  --frame:#000000;
}
*{margin:0;padding:0;box-sizing:border-box}
html,body{width:1200px;height:1200px;overflow:hidden;background:var(--frame)}
.splash{
  position:absolute;left:111px;top:233px;width:978px;height:733px;overflow:hidden;
  font-family:"Poppins",sans-serif;color:var(--white);
  background:
    radial-gradient(ellipse 60% 50% at 10% 5%, #22ff22 0%, rgba(34,255,34,0) 70%),
    radial-gradient(ellipse 80% 60% at 40% 40%, #1bd11b 0%, rgba(27,209,27,0) 70%),
    linear-gradient(135deg,#18e018 0%,#0f9e1a 40%,#0b7a1a 70%,#0a5e16 100%);
}
.backdrop{position:absolute;inset:0}
.title-card{
  position:absolute;left:229px;top:0;width:520px;height:178px;background:var(--white);
  border-radius:0 0 26px 26px;display:flex;align-items:center;justify-content:center;
}
.title-card h1{
  color:var(--brand-green);font-weight:700;font-size:40px;line-height:43px;text-align:center;letter-spacing:.2px;
}
.device{position:absolute}
.pc{left:79px;top:232px;width:238px;height:188px;border-radius:16px;
  background:#1c1c1c;border:3px solid #e8e8e8;box-shadow:0 4px 10px rgba(0,0,0,.35)}
.pc .screen{position:absolute;left:20px;top:17px;width:190px;height:142px;
  background:linear-gradient(180deg,#f2f2f2,#dfe9e0);border-radius:2px}
.ap{left:861px;top:230px;width:34px;height:194px;border-radius:6px;
  background:linear-gradient(90deg,#dcdcdc,#ffffff 45%,#d0d0d0)}
.label{position:absolute;text-transform:uppercase;line-height:1}
.label strong{display:block;font-weight:700;font-size:22px;letter-spacing:1.2px}
.label span{display:block;font-weight:400;font-size:16px;letter-spacing:.8px;margin-top:3px}
.label-pc{left:332px;top:308px}
.label-ap{right:128px;top:308px;text-align:right}
.label-cable{left:0;width:978px;top:440px;text-align:center}
.cable{position:absolute;inset:0}
.help-card{
  position:absolute;left:240px;top:554px;width:498px;height:179px;background:var(--white);
  border-radius:24px 24px 0 0;color:var(--brand-green);padding:12px 10px 0 28px;
}
.help-card h2{font-size:17px;font-weight:600;text-align:center;letter-spacing:.8px;margin-left:-18px;margin-bottom:2px}
.help-card ul{list-style:none;font-size:12px;line-height:13.8px}
.help-card li{padding-left:8px;text-indent:-8px}
.help-card li::before{content:"• "}
.help-card ul ul{padding-left:7px;text-indent:0}
</style>
</head>
<body>
<main class="splash">
  <svg class="backdrop" width="978" height="733" viewBox="0 0 978 733" aria-hidden="true">
    <g fill="none" stroke="#7dff7d" stroke-opacity=".35" stroke-width="1.2">
      <path d="M0 178 C120 178 160 170 228 100"/>
      <path d="M0 620 L240 620"/>
      <path d="M0 680 C120 660 170 640 240 640"/>
      <path d="M738 400 C850 420 930 380 978 300"/>
      <path d="M738 560 C850 540 920 520 978 460"/>
      <path d="M738 700 C860 680 930 640 978 580"/>
    </g>
    <g fill="none" stroke="#40ff40" stroke-opacity=".25" stroke-width="14">
      <path d="M0 340 C180 250 420 360 600 270 C720 210 800 240 978 120"/>
    </g>
    <g fill="#baffba">
      <circle cx="877" cy="33" r="4"/><circle cx="203" cy="498" r="5"/>
      <circle cx="116" cy="62" r="2"/><circle cx="99" cy="143" r="2"/>
      <circle cx="157" cy="148" r="2"/><circle cx="525" cy="301" r="2"/>
      <circle cx="527" cy="381" r="2"/><circle cx="347" cy="210" r="2"/>
    </g>
  </svg>

  <header class="title-card">
    <h1>Waiting for<br>connection to Wi-Fi<br>access point...</h1>
  </header>

  <div class="device pc" role="img" aria-label="Rugged tractor cab computer showing the seeding application dashboard">
    <div class="screen"></div>
  </div>

  <div class="device ap" role="img" aria-label="Outdoor Wi-Fi access point with two antennas"></div>

  <svg class="cable" width="978" height="733" viewBox="0 0 978 733" aria-hidden="true">
    <g fill="none" stroke="#ffffff" stroke-width="5" stroke-linecap="round" stroke-dasharray="0 11.3">
      <path d="M198 435 V474 H729 V387 H849"/>
    </g>
  </svg>

  <div class="label label-pc"><strong>Tractor Cab</strong><span>Computer</span></div>
  <div class="label label-ap"><strong>Wi-Fi Access Point</strong><span>NORLINK AX200-OUTDOOR</span></div>
  <div class="label label-cable"><strong>Ethernet Cable</strong></div>

  <section class="help-card">
    <h2>TROUBLESHOOTING STEPS:</h2>
    <ul>
      <li>This screen should only be visible for a short time on boot.</li>
      <li>If this screen stays visible for more than a minute:
        <ul>
          <li>Verify that the Wi-Fi Access Point (AP) powers up when this system does (indicated by a green light on the side of the AP).</li>
          <li>Check the Ethernet cable between this system and the AP for damage, and replace it if necessary.</li>
          <li>Power-cycle this system and wait for it to reboot fully.</li>
          <li>If the issue persists, contact KTWG support for further assistance.</li>
        </ul>
      </li>
    </ul>
  </section>

  <div class="brand-badge" style="position:absolute;left:856px;top:615px;width:89px;height:89px;border-radius:20px;background:var(--ink);border:3px solid var(--white);display:flex;align-items:center;justify-content:center;"><span style="font-weight:700;font-size:22px;color:var(--bright-green);letter-spacing:.5px">KTWG</span></div>
</main>
</body>
</html>
```